Varlomatch E-commerce Website Design

I'm looking into having my e-comm website built. We are an investment company that is investing in a private label focused on a rising sport category called Pickleball in EU market.

We will provide top quality material and acessories for players be ready to go to courts. We will have a range of: Rackets, Set of balls, Net, Lines, overgrip, water bottle, player bag.

As it´s a new sports category we would like to see an architecture that alows us to share some storytelling about the category, the brand and lead to purchase of our products.

We will position our self as an inclusive and fun brand that you can reach out to find more info about Pickleball Sport, buy your pickleball stuff and have fun. Its all about action and fun.

Target Market(s)

Europe Market

Industry/Entity Type

Pickleball (Sports)

Coding

Coded - Design and coding required

Number of Pages Required

1 page

Requirements
Must have
• E-commerce look and feel
Nice to have
• A bit of storytelling about the brand and specially the category (Pickleball).

```html
<!DOCTYPE html>
<html lang="en">
<head>
<meta charset="utf-8">
<title>Varlomatch – Pickleball Store</title>
<link href="https://fonts.googleapis.com/css2?family=Bebas+Neue&family=Nunito+Sans:wght@300;400;600;700;800&display=swap" rel="stylesheet">
<style>
:root{
  --teal:#5ccaa8;
  --teal-dark:#3fb48f;
  --ink:#111;
  --text:#333;
  --muted:#555;
  --card:#ececec;
  --line:#d4d4d4;
  --footer:#f4f4f4;
  --white:#fff;
}
*{box-sizing:border-box;margin:0;padding:0}
html,body{width:1200px;height:3186px;overflow:hidden;background:var(--white)}
body{position:relative;font-family:"Nunito Sans",sans-serif;color:var(--text)}
.abs{position:absolute}
.display{font-family:"Bebas Neue",sans-serif;color:var(--ink);letter-spacing:.5px}
.btn{position:absolute;background:var(--teal);color:#1d3b31;border-radius:20px;font-size:15px;display:flex;align-items:center;justify-content:center}
.arrow{position:absolute;width:30px;height:30px;border-radius:50%;background:var(--teal);display:flex;align-items:center;justify-content:center}

/* header */
.site-header{position:absolute;left:0;top:0;width:1200px;height:104px}
.brand{position:absolute;left:145px;top:34px;font-size:36px}
.nav a{position:absolute;top:45px;font-size:14px;color:var(--text);text-decoration:none}
.nav a.active{font-weight:700;color:var(--ink)}
.header-icon{position:absolute;top:42px}

/* hero */
.hero{position:absolute;left:0;top:104px;width:1200px;height:487px;
  background:linear-gradient(100deg,#2a3a33 0%,#425a4b 35%,#5b6e5e 60%,#4a6279 80%,#3a4a44 100%)}
.hero-small{position:absolute;left:146px;top:258px;font-size:34px;color:var(--white)}
.hero-big{position:absolute;left:146px;top:302px;font-size:60px;color:var(--white);line-height:1}
.hero-text{position:absolute;left:146px;top:378px;width:340px;font-size:16px;line-height:27px;color:#f1f1f1}
.mini-card{position:absolute;top:492px;width:212px;height:78px;background:var(--white);border-radius:3px;overflow:hidden}
.mini-card .thumb{position:absolute;left:6px;top:4px;width:86px;height:70px;border-radius:2px}
.mini-card .thumb.teal{left:0;top:0;height:78px;background:var(--teal)}
.mini-card .name{position:absolute;left:102px;top:8px;font-size:14px;color:var(--ink)}
.mini-card .price{position:absolute;left:102px;top:26px;font-size:16px;font-weight:700;color:var(--ink)}
.mini-card .buy{position:absolute;left:104px;top:52px;font-size:10px;color:var(--teal-dark)}

/* about */
.about-photo{position:absolute;left:0;top:674px;width:466px;height:307px}
.section-title{position:absolute;font-size:40px}
.about-text{position:absolute;left:541px;top:775px;width:486px;font-size:16px;line-height:27px;text-align:justify;font-weight:300}

/* products */
.tab{position:absolute;top:1164px;height:52px;border:1px solid var(--line);border-radius:3px;font-size:16px;font-weight:300;display:flex;align-items:center;justify-content:center;color:var(--text)}
.tab.active{border-color:var(--teal)}
.product{position:absolute;width:170px}
.product .box{width:170px;height:199px;background:var(--card);border-radius:6px;position:relative}
.product .box .shot{position:absolute;left:25px;top:35px;width:120px;height:120px;border-radius:10px}
.product .title{font-size:15px;font-weight:300;margin-top:13px;padding-left:13px}
.product .cost{font-size:15px;font-weight:700;color:var(--ink);padding-left:13px;margin-top:2px}

/* latest */
.promo{position:absolute;top:2040px;width:436px;height:290px;box-shadow:0 0 6px rgba(0,0,0,.08)}
.promo .visual{position:absolute;left:0;top:0;width:100%;height:215px}
.promo .band{position:absolute;left:0;bottom:0;width:100%;height:75px;background:var(--teal);padding:14px 28px;color:var(--ink)}
.promo .band strong{display:block;font-size:18px;font-weight:700;letter-spacing:.3px}
.promo .band span{font-size:18px;font-weight:600}

/* testimonials */
.quote{position:absolute;top:2528px;width:277px;height:278px;border:1px solid var(--teal);background:var(--white);padding:54px 16px 0}
.quote p{font-size:11px;line-height:20px;text-align:justify;color:#222}
.quote .who{text-align:center;font-weight:700;font-size:17px;color:var(--ink);margin-top:20px}
.quote .where{text-align:center;font-size:15px;margin-top:6px;color:var(--ink)}
.quote svg.tail{position:absolute;left:195px;bottom:-22px}

/* footer */
.site-footer{position:absolute;left:0;top:2901px;width:1200px;height:285px;background:var(--footer)}
.foot-col{position:absolute;top:54px}
.foot-col h4{font-size:18px;font-weight:700;color:var(--ink);margin-bottom:6px}
.foot-col a{display:block;font-size:18px;font-weight:300;color:var(--text);text-decoration:none;line-height:27.5px}
.social{position:absolute;top:112px;width:44px;height:44px;border-radius:50%;background:var(--teal)}
.foot-rule{position:absolute;left:0;top:214px;width:1200px;height:1px;background:#ccc}
.copy{position:absolute;left:147px;top:240px;font-size:12px;color:var(--muted)}
</style>
</head>
<body>

<header class="site-header">
  <div class="brand display">Varlomatch</div>
  <nav class="nav">
    <a class="active" href="#" style="left:567px">Home</a>
    <a href="#" style="left:660px">About Us</a>
    <a href="#" style="left:773px">Shop</a>
    <a href="#" style="left:861px">Contact</a>
  </nav>
  <svg class="header-icon" style="left:938px" width="24" height="24" viewBox="0 0 24 24"><circle cx="10" cy="10" r="7" fill="none" stroke="#111" stroke-width="2.4"/><line x1="15" y1="15" x2="22" y2="22" stroke="#111" stroke-width="2.6" stroke-linecap="round"/></svg>
  <svg class="header-icon" style="left:989px;top:41px" width="26" height="26" viewBox="0 0 26 26"><circle cx="13" cy="13" r="12" fill="#dfe8f7"/><circle cx="13" cy="10" r="4.5" fill="#2f6fd6"/><path d="M5 21c2-4 5-5.5 8-5.5s6 1.5 8 5.5" fill="#2f6fd6"/></svg>
  <svg class="header-icon" style="left:1042px;top:38px" width="32" height="30" viewBox="0 0 32 30"><path d="M2 5h5l4 15h15l3-11H9" fill="#f2c230" stroke="#111" stroke-width="2" stroke-linejoin="round"/><circle cx="13" cy="25" r="2.3" fill="#111"/><circle cx="24" cy="25" r="2.3" fill="#111"/><circle cx="26" cy="5" r="4.5" fill="#111"/><text x="26" y="7.5" font-size="7" fill="#fff" text-anchor="middle" font-family="Nunito Sans,sans-serif">2</text></svg>
</header>

<section class="hero" role="img" aria-label="Player in a blue shirt and white cap striking a ball with a pickleball paddle on an outdoor court">
</section>
<div class="hero-small display">Welcome to</div>
<div class="hero-big display">Varlomatch</div>
<p class="hero-text">Lorem ipsum dolor sit amet, sed do eiusmod tempor ut labore et dolore magna aliqua.</p>
<div class="btn" style="left:146px;top:453px;width:162px;height:38px">Get Started</div>

<div class="arrow" style="left:456px;top:517px"><svg width="12" height="12" viewBox="0 0 12 12"><path d="M8 1L3 6l5 5" fill="none" stroke="#fff" stroke-width="2"/></svg></div>
<div class="mini-card" style="left:475px">
  <div class="thumb" role="img" aria-label="Blue pickleball paddle with balls" style="background:radial-gradient(circle at 50% 45%,#6c8fd8,#f3f3f3 70%)"></div>
  <div class="name">Pickleball Bat</div><div class="price">$23.00</div><div class="buy">Buy Now ⟶</div>
</div>
<div class="mini-card" style="left:700px">
  <div class="thumb" role="img" aria-label="Set of four coloured pickleballs" style="background:radial-gradient(circle at 50% 50%,#c7e06a,#f3f3f3 70%)"></div>
  <div class="name">Pickleball Bat</div><div class="price">$23.00</div><div class="buy">Buy Now ⟶</div>
</div>
<div class="mini-card" style="left:925px">
  <div class="thumb teal" role="img" aria-label="Orange and blue water bottles"></div>
  <div class="name">Pickleball Bat</div><div class="price">$23.00</div><div class="buy">Buy Now ⟶</div>
</div>
<div class="arrow" style="left:1128px;top:517px"><svg width="12" height="12" viewBox="0 0 12 12"><path d="M4 1l5 5-5 5" fill="none" stroke="#fff" stroke-width="2"/></svg></div>

<section aria-label="About pickleball">
  <svg class="about-photo" viewBox="0 0 466 307" role="img" aria-label="Player in orange patterned sleeve reaching low for a ball with a paddle on a blue court">
    <defs><linearGradient id="court" x1="0" y1="0" x2="1" y2="1"><stop offset="0" stop-color="#4a6f9c"/><stop offset=".55" stop-color="#2d4a74"/><stop offset="1" stop-color="#6b3c3c"/></linearGradient></defs>
    <path d="M108 10h348v220c0 45-25 77-70 77H120L10 210V100z" fill="var(--teal)"/>
    <path d="M98 0h340c10 0 18 8 18 18v240c0 22-16 38-38 38H105L0 200V96z" fill="url(#court)"/>
  </svg>
  <h2 class="section-title display" style="left:540px;top:714px">About Pickleball</h2>
  <p class="about-text">Lorem ipsum dolor sit amet, consectetur adipiscing elit, sed do eiusmod tempor incididunt ut labore et dolore magna aliqua. Quis ipsum suspendisse ultrices gravida. Risus commodo viverra maecenas accumsan lacus vel facilisis.</p>
  <div class="btn" style="left:539px;top:909px;width:164px;height:39px">Read More</div>
</section>

<section aria-label="Top selling products">
  <h2 class="section-title display" style="left:0;width:1185px;text-align:center;top:1074px">Top Selling Products</h2>
  <div class="arrow" style="left:93px;top:1175px"><svg width="12" height="12" viewBox="0 0 12 12"><path d="M8 1L3 6l5 5" fill="none" stroke="#fff" stroke-width="2"/></svg></div>
  <div class="tab active" style="left:148px;width:66px">All</div>
  <div class="tab" style="left:240px;width:120px">Rackets</div>
  <div class="tab" style="left:387px;width:120px">Set of balls</div>
  <div class="tab" style="left:533px;width:86px">Net</div>
  <div class="tab" style="left:644px;width:120px">Lines</div>
  <div class="tab" style="left:790px;width:122px">Overgrip</div>
  <div class="tab" style="left:938px;width:120px">Water bottle</div>
  <div class="arrow" style="left:1077px;top:1175px"><svg width="12" height="12" viewBox="0 0 12 12"><path d="M4 1l5 5-5 5" fill="none" stroke="#fff" stroke-width="2"/></svg></div>

  <div class="product" style="left:139px;top:1260px"><div class="box"><div class="shot" role="img" aria-label="Orange and blue water bottles" style="background:radial-gradient(circle,#4aa3d8 0%,#d98a35 35%,var(--card) 70%)"></div></div><div class="title">Pickleball water bottle</div><div class="cost">$39.00</div></div>
  <div class="product" style="left:327px;top:1260px"><div class="box"><div class="shot" role="img" aria-label="Blue paddle with yellow balls" style="background:radial-gradient(circle,#5a7fd0 0%,#f0c24a 30%,var(--card) 70%)"></div></div><div class="title">Pickleball Racket</div><div class="cost">$39.00</div></div>
  <div class="product" style="left:516px;top:1260px"><div class="box"><div class="shot" role="img" aria-label="Four coloured pickleballs" style="background:radial-gradient(circle,#e36fd0 0%,#7ad04a 30%,#4aa3e8 50%,var(--card) 72%)"></div></div><div class="title">Pickleball Balls</div><div class="cost">$39.00</div></div>
  <div class="product" style="left:703px;top:1260px"><div class="box"><div class="shot" role="img" aria-label="Black overgrip tape rolls" style="background:radial-gradient(circle,#2b2b2b 0%,#777 30%,var(--card) 68%)"></div></div><div class="title">Pickleball Overgrip</div><div class="cost">$39.00</div></div>
  <div class="product" style="left:894px;top:1260px"><div class="box"><div class="shot" role="img" aria-label="Orange and black player bag" style="background:radial-gradient(ellipse,#e8642a 0%,#333 35%,var(--card) 70%)"></div></div><div class="title">Licence Plate Flipper</div><div class="cost">$39.00</div></div>

  <div class="product" style="left:139px;top:1538px"><div class="box"><div class="shot" role="img" aria-label="Black overgrip tape rolls" style="background:radial-gradient(circle,#2b2b2b 0%,#777 30%,var(--card) 68%)"></div></div><div class="title" style="padding-left:21px">Pickleball Overgrip</div><div class="cost" style="padding-left:21px">$39.00</div></div>
  <div class="product" style="left:328px;top:1538px"><div class="box"><div class="shot" role="img" aria-label="Orange and black player bag" style="background:radial-gradient(ellipse,#e8642a 0%,#333 35%,var(--card) 70%)"></div></div><div class="title">Licence Plate Flipper</div><div class="cost">$39.00</div></div>
  <div class="product" style="left:516px;top:1538px"><div class="box"><div class="shot" role="img" aria-label="Orange and blue water bottles" style="background:radial-gradient(circle,#4aa3d8 0%,#d98a35 35%,var(--card) 70%)"></div></div><div class="title">Pickleball water bottle</div><div class="cost">$39.00</div></div>
  <div class="product" style="left:704px;top:1538px"><div class="box"><div class="shot" role="img" aria-label="Blue paddle with yellow balls" style="background:radial-gradient(circle,#5a7fd0 0%,#f0c24a 30%,var(--card) 70%)"></div></div><div class="title">Pickleball Racket</div><div class="cost">$39.00</div></div>
  <div class="product" style="left:892px;top:1538px"><div class="box"><div class="shot" role="img" aria-label="Four coloured pickleballs" style="background:radial-gradient(circle,#e36fd0 0%,#7ad04a 30%,#4aa3e8 50%,var(--card) 72%)"></div></div><div class="title">Pickleball Balls</div><div class="cost">$39.00</div></div>

  <div class="btn" style="left:511px;top:1842px;width:161px;height:38px;font-size:16px">View More</div>
</section>

<section aria-label="Latest products">
  <h2 class="section-title display" style="left:0;width:1200px;text-align:center;top:1958px">Latest Products</h2>
  <div class="promo" style="left:147px">
    <div class="visual" role="img" aria-label="Hands wrapping white overgrip tape around a racket handle" style="background:linear-gradient(160deg,#8a6a58 0%,#c59b86 45%,#e7d6cf 80%,#f2ede9 100%)"></div>
    <div class="band"><strong>RACKET OVERGRIP</strong><span>Buy this Get 20% Off for other products</span></div>
  </div>
  <div class="promo" style="left:621px;height:287px">
    <div class="visual" role="img" aria-label="Orange and black pickleball player bag" style="background:radial-gradient(ellipse at 50% 55%,#e8642a 0%,#3a3a3a 28%,#f5f5f5 60%,#fff 100%)"></div>
    <div class="band"><strong>PICKLEBALL BAG</strong><span>Buy this and Get 20% Off for other products</span></div>
  </div>
</section>

<section aria-label="Testimonials">
  <h2 class="section-title display" style="left:0;width:1197px;text-align:center;top:2410px">Testimonials</h2>
  <p class="abs" style="left:0;width:1200px;text-align:center;top:2470px;font-size:16px;font-weight:300;color:#222">Lorem ipsum dolor sit amet, consectetur adipiscing elit, sed do eiusmod tempor incididunt ut labore et dolore magna aliqua.</p>
  <div class="arrow" style="left:93px;top:2647px"><svg width="12" height="12" viewBox="0 0 12 12"><path d="M8 1L3 6l5 5" fill="none" stroke="#fff" stroke-width="2"/></svg></div>
  <div class="quote" style="left:146px">
    <p>Lorem ipsum dolor sit amet, consectetur adipiscing elit, sed do eiusmod tempor incididunt ut labore et dolore magna aliqua. Ut enim ad minim veniam, quis nostrud exercitation ullamco laboris nisi ut aliquip ex ea commodo consequat. Duis aute irure dolor in reprehenderit in voluptate</p>
    <div class="who">Lena Hartwig</div><div class="where">USA</div>
    <svg class="tail" width="24" height="23" viewBox="0 0 24 23"><path d="M0 0L2 22L22 0" fill="#fff" stroke="var(--teal)"/></svg>
  </div>
  <div class="quote" style="left:464px">
    <p>Lorem ipsum dolor sit amet, consectetur adipiscing elit, sed do eiusmod tempor incididunt ut labore et dolore magna aliqua. Ut enim ad minim veniam, quis nostrud exercitation ullamco laboris nisi ut aliquip ex ea commodo consequat. Duis aute irure dolor in reprehenderit in voluptate</p>
    <div class="who">Lena Hartwig</div><div class="where">USA</div>
    <svg class="tail" width="24" height="23" viewBox="0 0 24 23"><path d="M0 0L2 22L22 0" fill="#fff" stroke="var(--teal)"/></svg>
  </div>
  <div class="quote" style="left:781px">
    <p>Lorem ipsum dolor sit amet, consectetur adipiscing elit, sed do eiusmod tempor incididunt ut labore et dolore magna aliqua. Ut enim ad minim veniam, quis nostrud exercitation ullamco laboris nisi ut aliquip ex ea commodo consequat.</p>
    <div class="who" style="margin-top:40px">Lena Hartwig</div><div class="where">USA</div>
    <svg class="tail" width="24" height="23" viewBox="0 0 24 23"><path d="M0 0L2 22L22 0" fill="#fff" stroke="var(--teal)"/></svg>
  </div>
  <div class="arrow" style="left:1077px;top:2647px"><svg width="12" height="12" viewBox="0 0 12 12"><path d="M4 1l5 5-5 5" fill="none" stroke="#fff" stroke-width="2"/></svg></div>
</section>

<footer class="site-footer">
  <div class="display" style="position:absolute;left:145px;top:44px;font-size:44px">Varlomatch</div>
  <div class="social" style="left:146px"></div>
  <div class="social" style="left:198px"></div>
  <div class="foot-col" style="left:438px"><h4>Quick Links</h4><a href="#">Home</a><a href="#">About Us</a><a href="#">Shop</a><a href="#">Contact</a></div>
  <div class="foot-col" style="left:678px"><h4>Support</h4><a href="#">Contact Us</a><a href="#">Refund Policy</a><a href="#">Terms of Service</a><a href="#">FAQ's</a></div>
  <div class="foot-col" style="left:929px"><h4>Help Links</h4><a href="#">Legal</a><a href="#">Privacy</a><a href="#">Terms of Use</a></div>
  <div class="foot-rule"></div>
  <div class="copy">© copyrights 2023 Varlomatch | &nbsp;All Rights Reserved</div>
</footer>

</body>
</html>
```